Q.B. Brightpath Store

The design is for eCommerce home page but I would like it to complement this site: http://www.qbbrightpathsolutions.com/ but... it should also have independence as a standalone site.

The best design will be able to effectively mix corporate with a high quality small business consumer feel. It should be completely custom design, not a template look or feel. I want the users to get the feeling that this is the place to go for buying tech for business. We sell the same products as RVK.

You can be creative as you wish, as long as the elements of a great eCommerce site are present.

I would like your 'design' to blow these away:
http://www.shopping.zl.com/
mirabelo.com
http://www.rvk.com/

Here are references:
Call to action
http://markvantage.com/us/blog/48153-seven-tips-for-designing-an-effective-ecommerce-call-to-action

Effective Ecommerce design
http://www.vexa.com/ss/7-tips-for-effective-e-commerce#0

91 points of ecommerce
http://qir.com/blog/holygrail-of-ecommerce-conversion-optimization-91-points-checklist

UPDATE 07/11/2013:

Please look at the category sample png files. I see already many people are using the main menu from qbbrightpathsolutions.com and I do not mind your creativiety, but this is an eCommerce store and people need a menu to get to the categories and/or product types. I don't want to limit anyone creativity by the png samples. I'm also not using them to show I like them in any particular way or form, just that it's needed, whether it's a button (dropdown of course) that says 'Categories' or 'Products, whether it an accordion, horizontal or vertical.

Thanks

UPDATE 07/12/2013:

Please find other use of space that has been used for About Us paragraph (if you've added it to the page). About Us should have it's own page and the purpose of the design should be to sell products (and some services as products). Please put a link or some other creative method to lead users to the About Us page.

Reason: I've raised the award, including 1st, 2nd, and 3rd place and participation payments so I will also extend 7 days. Thanks!

I've updated the product brief. Please scroll down to where it says: UPDATE 07/11/2013

Thanks!

UPDATE 07/12/2013:

Please find other use of space that has been used for About Us paragraph (if you've added it to the page).  About Us should have it's own page and the purpose of the design should be to sell products (and some services as products). Please put a link or some other creative method to lead users to the About Us page if you must but not on the real estate of the page.

Thanks!

Added updates to the brief 7/14/2013.

Thanks!

The voting is in and the project is complete.  Thanks everyone for joining, all of those who participated are truly amazingly talented. But, there were only 3 prizes.  I will be having further projects down the line to develop other pages to this site after the initial implementation is completed.  I truly would like to have you all back. 

- Thank you.

Target Market(s)

corporate decision-makers AND small business consumers

Industry/Entity Type

Small Business

Requirements
Must have
• Call to action.
Openness (non-clutter).

These elements:
Search box
Logo
Tagline
Telephone number
Contact details
Address
My account / sign in
Shopping basket / checkout link
Latest offers
Promotional area
Email sign up
Delivery information
About us
Link to press office / corporate site
Terms and conditions
Sitemap for the footer.
Delivery offers: free
Personalized recommendations
Social media links
Accepted payment methods
Link to blog or community section
Change language / country

http://smartplansblog.pelloware.com/sales-leads-landing-page/

UPDATE 07/14/2013
Category Menu. This can be a dropdown, horizontal, vertical, etc. But shoppers need to know how to get to the products they want to buy.
Nice to have
• Trustmarks
Blog/Blog link

UPDATE 07/12/2013:
Make the footer useful.

UPDATE 07/14/2013 (Suggestions of elements to differentiate your designs)

-Quick Shop: A quick buy module/section: Where a user can put in a SKU number or Model number to quickly add the product to their shopping cart.

-Featured
-Best Sellers
-Specials
-Trending Tags/Tag Cloud
- Activity Stream
- Cross Sell/ Up Sell
- Testimonial
- Social Network Feed
- Live Help
- Feedback/Support/Contact Tab
- Show logged in user (i.e. Welcome, Mark Pelley)
Should not have
• The design SHOULD NOT be generic like this:

http://www.artgatherly.com/design/52392
http://www.falconmart.com/

The page should not feel over cluttered. It should not have low quality icons or design elements. Navigation should not be hard to discover or confusing.

```html
<!DOCTYPE html>
<html lang="en">
<head>
<meta charset="utf-8">
<title>Q.B. Brightpath Store</title>
<link href="https://fonts.googleapis.com/css2?family=Open+Sans:wght@400;600;700&family=PT+Sans+Narrow:wght@400;700&family=Arimo:wght@400;700&display=swap" rel="stylesheet">
<style>
:root{
  --blue:#0f6fb8;
  --blue-dark:#0a5a98;
  --blue-band:#1a80c6;
  --navy:#0b3f66;
  --black:#0d0d0d;
  --ink:#222;
  --grey-text:#777;
  --panel:#e9e9e9;
  --panel-dark:#6a6a6a;
  --filter-bg:#e2edf6;
  --price:#d9232d;
  --star:#f4c21a;
  --star-off:#ddd;
  --orange:#f47a1f;
  --white:#fff;
}
*{box-sizing:border-box;margin:0;padding:0}
html,body{width:724px;height:1200px;overflow:hidden;background:var(--white)}
body{position:relative;font-family:"Open Sans",sans-serif;color:var(--ink)}
.abs{position:absolute}
a{color:inherit;text-decoration:none}

/* top bar */
.topbar{left:0;top:0;width:724px;height:33px;background:var(--black);color:#ccc;font:600 7px/33px "Open Sans",sans-serif;text-transform:uppercase}
.topbar .links{position:absolute;right:88px;top:0;word-spacing:1px}
.topbar .sep{margin:0 6px;color:#777}

/* header */
.logo{left:61px;top:40px;display:flex;align-items:center;gap:6px}
.logo .mark{width:30px;height:30px;border-radius:50%;background:var(--blue)}
.logo .name{font:700 13px/1 "Open Sans",sans-serif;color:var(--blue);letter-spacing:.3px}
.search{left:398px;top:44px;width:130px;height:21px;border:1px solid #ddd;border-radius:3px;font-size:7px;color:#777;padding:6px 9px;box-shadow:0 2px 3px rgba(0,0,0,.06)}
.search svg{position:absolute;right:6px;top:4px}
.lang{left:533px;top:44px;width:57px;height:21px;border:1px solid #ddd;border-radius:3px;font-size:7px;padding:5px 6px;display:flex;align-items:center;gap:4px}
.lang .flag{width:10px;height:7px;background:#c8102e;border:1px solid #1f3f8f}
.cart{left:600px;top:40px;width:28px;height:28px;border-radius:50%;background:#e8eef4;border:1px solid #d3dde6;display:flex;align-items:center;justify-content:center}
.call{right:103px;top:77px;font:700 11.5px/1 "Open Sans",sans-serif;color:var(--blue-band)}

/* nav */
.mainnav{left:0;top:97px;width:724px;height:26px;background:linear-gradient(#1b82c9,var(--blue-dark))}
.mainnav ul{list-style:none;display:flex;margin-left:82px;gap:0}
.mainnav li{font:400 11px/26px "PT Sans Narrow",sans-serif;color:var(--white);text-transform:uppercase;margin-right:20px;letter-spacing:.2px}

/* hero */
.deal{left:60px;top:126px;width:182px;height:222px;background:var(--panel)}
.deal h2{position:absolute;left:14px;top:40px;font:400 29px/1 "Open Sans",sans-serif;color:#111}
.deal p{position:absolute;left:14px;top:78px;width:156px;font-size:7.4px;line-height:10.5px;text-align:justify;color:#222}
.deal .divider{position:absolute;left:0;top:132px;width:182px;height:1px;background:#d6d6d6}
.deal .value,.deal .price{position:absolute;right:10px;font-size:9.5px;color:#222}
.deal .value{top:139px}.deal .price{top:158px}
.deal .grab{position:absolute;left:0;bottom:0;width:182px;height:44px;background:var(--panel-dark);color:var(--white);font-size:9px;line-height:11px;text-align:right;padding:9px 12px 0 0}
.hero-photo{left:264px;top:146px;width:400px;height:202px;background:linear-gradient(160deg,#f4f4f4,#d9d9d9 55%,#eeeeee)}
.hero-photo .slab1{position:absolute;left:4px;top:6px;width:170px;height:134px;border-radius:8px;background:linear-gradient(140deg,#3a3a3a,#111)}
.hero-photo .slab2{position:absolute;left:140px;top:24px;width:190px;height:150px;border-radius:8px;background:linear-gradient(140deg,#4a4a4a,#1a1a1a)}
.hero-photo .slab2 i{position:absolute;left:10px;top:12px;right:10px;bottom:12px;background:linear-gradient(135deg,#6c5a8e,#8a6d55 50%,#3f6e9c);border-radius:2px}
.offer{left:520px;top:232px}
.offer-text{right:76px;top:296px;color:var(--white);text-align:center;line-height:1}
.offer-text b{display:block;font:400 22px "Open Sans",sans-serif}
.offer-text span{font:400 12px "Open Sans",sans-serif;color:#f5c542}
.hero-shadow{left:60px;top:348px;width:604px;height:6px;background:radial-gradient(ellipse at center,rgba(0,0,0,.18),transparent 70%)}
.dots{left:340px;top:351px;display:flex;gap:5px}
.dots i{width:7px;height:7px;border-radius:50%;background:var(--blue-band)}
.dots i:nth-child(2){background:#9cc4e4}

/* delivery band */
.band{left:0;top:367px;width:724px;height:60px;background:var(--blue-band);color:var(--white)}
.band .free{position:absolute;left:97px;top:15px;font:700 19px/1 "Open Sans",sans-serif;letter-spacing:.2px}
.band .free small{display:block;font:700 7px/1 "Open Sans",sans-serif;margin-top:5px;margin-left:2px}
.band .scooter{position:absolute;left:258px;top:4px;width:96px;height:52px;background:linear-gradient(120deg,#f39a2b,#e0611a);border-radius:6px}
.band .login{position:absolute;left:400px;top:0;width:108px;height:60px;background:var(--navy);display:flex;align-items:center;gap:10px;padding-left:20px;font:700 11.5px "Open Sans",sans-serif;letter-spacing:1px}
.band .register{position:absolute;left:522px;top:0;height:60px;display:flex;align-items:center;gap:12px;font:700 11.5px "Open Sans",sans-serif;letter-spacing:1px}

/* filter */
.filter{left:0;top:427px;width:724px;height:45px;background:var(--filter-bg)}
.filter .label{position:absolute;top:17px;font:400 10.5px/1 "PT Sans Narrow",sans-serif;color:var(--blue-band);font-size:11px;text-transform:uppercase}
.filter .select{position:absolute;top:17px;height:17px;background:var(--white);border:1px solid #ccd;font-size:7px;padding:4px 6px;color:#444}
.filter .select::after{content:"";position:absolute;right:6px;top:6px;border:3px solid transparent;border-top-color:#666}
.filter .select::before{content:"";position:absolute;right:16px;top:2px;width:1px;height:11px;background:#ddd}
.filter .btn{position:absolute;left:603px;top:17px;width:48px;height:17px;background:var(--blue);color:var(--white);font:600 8px/17px "Open Sans",sans-serif;text-align:center}

/* features */
.feature{top:484px;width:180px}
.feature .icon{position:absolute;left:0;top:0;width:28px;height:26px;border-radius:4px}
.feature h3{position:absolute;left:36px;top:6px;font:700 11px/1 "PT Sans Narrow",sans-serif;text-transform:uppercase;color:#222;white-space:nowrap;font-size:12px}
.feature p{position:absolute;left:3px;top:30px;width:180px;font-size:7px;line-height:12px;color:var(--grey-text)}

/* tabs */
.tabs{left:73px;top:582px;display:flex;gap:2px}
.tabs span{height:22px;font:400 11px/22px "PT Sans Narrow",sans-serif;text-transform:uppercase;padding:0 10px;background:#e6e6e6;color:#555;border:1px solid #d6d6d6;border-bottom:0}
.tabs .on{background:var(--blue);color:var(--white);border-color:var(--blue)}
.tabs span:nth-child(2){padding:0 14px}
.products{left:72px;top:604px;width:580px;height:244px;background:#eeeeee;border:1px solid #dcdcdc}
.card{position:absolute;top:8px;width:133px;height:222px;background:var(--white);border:1px solid #ddd}
.card .photo{position:absolute;left:4px;top:4px;width:123px;height:126px;border:1px solid #eee}
.card .photo i{position:absolute;left:34px;top:12px;width:56px;height:104px;border-radius:8px}
.card h4{position:absolute;top:138px;width:100%;text-align:center;font:400 8.5px "Open Sans",sans-serif;color:#222;text-transform:uppercase}
.card .price{position:absolute;left:8px;top:155px;font:400 10px "Arimo",sans-serif;color:var(--price)}
.card .add{position:absolute;right:4px;top:153px;width:58px;height:16px;background:var(--blue);color:var(--white);font:600 6.5px/16px "Open Sans",sans-serif;text-align:center;border-radius:2px}
.card .meta{position:absolute;left:0;top:178px;width:100%;height:42px;background:#f1f1f1;border-top:1px solid #e6e6e6}
.card .stars{position:absolute;left:31px;top:5px;display:flex;gap:1px}
.card .links{position:absolute;top:26px;width:100%;text-align:center;font-size:6.4px;color:#888}
.arrow{top:700px;width:19px;height:42px;background:var(--blue);display:flex;align-items:center;justify-content:center}

/* about */
.about h2{position:absolute;left:0;top:856px;width:724px;text-align:center;font:700 14px/1 "PT Sans Narrow",sans-serif;text-transform:uppercase;color:#222}
.about p{position:absolute;left:86px;top:879px;width:552px;text-align:center;font-size:7.4px;line-height:12px;color:var(--grey-text)}
.readmore{left:333px;top:937px;width:58px;height:17px;background:var(--blue);color:var(--white);font-size:8px;line-height:17px;text-align:center;border-radius:2px}

/* brands */
.brands{left:72px;top:970px;width:580px;height:36px;background:#f3f3f3;border:1px solid #e0e0e0}
.brands .name{position:absolute;top:10px;font-size:15px;line-height:1;font-family:"Open Sans",sans-serif}
.brands svg{position:absolute;top:11px}

/* footer */
.footer{left:0;top:1014px;width:724px;height:186px;background:var(--black);color:var(--white);font-family:"Arimo",sans-serif}
.footer h5{position:absolute;top:16px;font:400 11px "Arimo",sans-serif}
.footer .line{position:absolute;font-size:7.3px;line-height:12.5px}
.footer .dot{position:absolute;width:18px;height:18px;border-radius:50%;background:var(--orange);display:flex;align-items:center;justify-content:center}
.footer ul{position:absolute;top:38px;list-style:none;font-size:7.3px;line-height:15.7px}
.footer ul li::before{content:"›";margin-right:6px;font-size:9px}
.footer .email{position:absolute;left:462px;top:38px;width:138px;height:19px;background:var(--white);border:1px solid #ccc;border-radius:2px;font-size:7px;color:#aaa;padding:5px 6px}
.footer .submit{position:absolute;left:608px;top:38px;width:31px;height:19px;background:var(--orange);border-radius:3px;font-size:7.5px;line-height:19px;text-align:center}
.footer .social{position:absolute;top:142px;width:20px;height:20px;border-radius:2px}
.copy{position:absolute;left:542px;top:1174px;font-size:7px;color:var(--white);font-family:"Arimo",sans-serif}
</style>
</head>
<body>

<div class="abs topbar"><div class="links">Go Shopping | Billing | Get Support<span class="sep"> </span> My Account <span class="sep">|</span> Check Out <span class="sep">|</span> Sign In</div></div>

<header>
  <div class="abs logo"><span class="mark"></span><span class="name">Q.B. Brightpath<br>Solutions</span></div>
  <div class="abs search">Search
    <svg width="11" height="11" viewBox="0 0 11 11"><circle cx="4.5" cy="4.5" r="3.5" fill="none" stroke="#888" stroke-width="1.2"/><path d="M7 7l3 3" stroke="#888" stroke-width="1.4"/></svg>
  </div>
  <div class="abs lang"><span class="flag"></span>Eng<svg width="6" height="4" viewBox="0 0 6 4" style="margin-left:6px"><path d="M0 0h6L3 4z" fill="#555"/></svg></div>
  <div class="abs cart"><svg width="14" height="12" viewBox="0 0 14 12"><path d="M1 1h2l2 7h6l2-5H4" fill="none" stroke="var(--blue)" stroke-width="1.4"/><circle cx="6" cy="10.5" r="1" fill="var(--blue)"/><circle cx="10" cy="10.5" r="1" fill="var(--blue)"/></svg></div>
  <div class="abs call">CALL US : +1 (888) XXX XXXX</div>
</header>

<nav class="abs mainnav"><ul><li>Hardware</li><li>Software</li><li>Brands</li><li>Best Deals</li><li>Product Finders</li><li>Favorites</li><li>IT Resources</li><li>Technology</li></ul></nav>

<section class="hero">
  <div class="abs deal">
    <h2>Save 50%</h2>
    <p>Lorem ipsum dolor sit amet, consectetur adipisicing elit, sed do eiusmod tempor incididunt ut labore et dolore magna aliqua. Ut enim ad minim veniam, quis....</p>
    <div class="divider"></div>
    <div class="value">Value: $30</div>
    <div class="price">Deal Price: $15</div>
    <div class="grab">Grab It By: Jul 03, 2013<br>Source: DealHarbor</div>
  </div>
  <div class="abs hero-photo" role="img" aria-label="Two tablet computers, one showing its back and one showing its home screen"><span class="slab1"></span><span class="slab2"><i></i></span></div>
  <svg class="abs offer" width="144" height="116" viewBox="0 0 144 116"><path d="M144 0V116H0z" fill="var(--blue-band)"/></svg>
  <div class="abs offer-text"><b>50%</b><span>Offer</span></div>
  <div class="abs hero-shadow"></div>
  <div class="abs dots"><i></i><i></i><i></i><i></i></div>
</section>

<section class="abs band">
  <div class="free">FREE DELIVERY<small>RESTRICTIONS APPLY.  SEE DETAIL</small></div>
  <div class="scooter" role="img" aria-label="Courier on an orange delivery scooter"></div>
  <div class="login"><svg width="18" height="22" viewBox="0 0 18 22"><path d="M4 10V6a5 5 0 0 1 10 0v4" fill="none" stroke="#ccc" stroke-width="2"/><rect x="1" y="10" width="16" height="12" rx="2" fill="#bbb"/></svg>LOGIN</div>
  <div class="register"><svg width="22" height="26" viewBox="0 0 22 26"><path d="M2 2h13l5 5v17H2z" fill="#fff"/><path d="M6 22l8-14 3 2-8 14z" fill="#f5b82e"/></svg>REGISTER</div>
</section>

<section class="abs filter">
  <span class="label" style="left:75px">Shop by Product</span>
  <span class="select" style="left:166px;width:112px">Hardware</span>
  <span class="select" style="left:286px;width:112px">Tablets</span>
  <span class="label" style="left:406px">Shop by Brand</span>
  <span class="select" style="left:482px;width:112px">Select Brand</span>
  <span class="btn">FILTER</span>
</section>

<section class="features">
  <div class="abs feature" style="left:76px"><span class="icon" style="background:linear-gradient(#8bc34a,#4f8f1f)" role="img" aria-label="Free shipping tag with scissors"></span><h3>Free Worldwide Shipping</h3><p>There are many variations of passages of Lorem Ipsum available, but the majority have suffered alteration in some form, by injected humour, or randomised words which don't look even slightly believable.</p></div>
  <div class="abs feature" style="left:278px"><span class="icon" style="background:radial-gradient(#e53935,#b71c1c)" role="img" aria-label="Warranty rosette"></span><h3>12 Months Warranty</h3><p>There are many variations of passages of Lorem Ipsum available, but the majority have suffered alteration in some form, by injected humour, or randomised words which don't look even slightly believable.</p></div>
  <div class="abs feature" style="left:476px"><span class="icon" style="background:linear-gradient(#f6c48a,#d9893a)" role="img" aria-label="Support agent illustration"></span><h3>Testimonials</h3><p>There are many variations of passages of Lorem Ipsum available, but the majority have suffered alteration in some form, by injected humour, or randomised words which don't look even slightly believable.</p></div>
</section>

<div class="abs tabs"><span class="on">Featured</span><span>Recommended</span><span>Specials</span></div>
<section class="abs products">
  <div class="card" style="left:10px"><div class="photo" role="img" aria-label="Phone in a blue flip case"><i style="background:linear-gradient(135deg,#2c5fd0,#163a8c)"></i></div><h4>Demo Item</h4><span class="price">$7678.64</span><span class="add">ADD TO CART</span><div class="meta"><div class="stars"><svg width="66" height="11" viewBox="0 0 66 11"><g fill="var(--star)"><path id="s" d="M5.5 0l1.6 3.6 3.9.4-2.9 2.6.9 3.9-3.5-2-3.5 2 .9-3.9L0 4l3.9-.4z"/><use href="#s" x="13"/><use href="#s" x="26"/></g><g fill="var(--star-off)"><use href="#s" x="39"/><use href="#s" x="52"/></g></svg></div><div class="links">+ Add to Wishlist &nbsp; + Add to Compare</div></div></div>
  <div class="card" style="left:152px"><div class="photo" role="img" aria-label="Two black phone cases"><i style="background:linear-gradient(135deg,#333,#111)"></i></div><h4>Demo Item</h4><span class="price">$7678.64</span><span class="add">ADD TO CART</span><div class="meta"><div class="stars"><svg width="66" height="11" viewBox="0 0 66 11"><g fill="var(--star)"><use href="#s"/><use href="#s" x="13"/><use href="#s" x="26"/></g><g fill="var(--star-off)"><use href="#s" x="39"/><use href="#s" x="52"/></g></svg></div><div class="links">+ Add to Wishlist &nbsp; + Add to Compare</div></div></div>
  <div class="card" style="left:294px"><div class="photo" role="img" aria-label="Phone in a slim black case"><i style="background:linear-gradient(135deg,#2b2b2b,#050505)"></i></div><h4>Demo Item</h4><span class="price">$7678.64</span><span class="add">ADD TO CART</span><div class="meta"><div class="stars"><svg width="66" height="11" viewBox="0 0 66 11"><g fill="var(--star)"><use href="#s"/><use href="#s" x="13"/><use href="#s" x="26"/></g><g fill="var(--star-off)"><use href="#s" x="39"/><use href="#s" x="52"/></g></svg></div><div class="links">+ Add to Wishlist &nbsp; + Add to Compare</div></div></div>
  <div class="card" style="left:436px"><div class="photo" role="img" aria-label="Phone in a lime green case"><i style="background:linear-gradient(135deg,#c8cf2a,#8e9416)"></i></div><h4>Demo Item</h4><span class="price">$7678.64</span><span class="add">ADD TO CART</span><div class="meta"><div class="stars"><svg width="66" height="11" viewBox="0 0 66 11"><g fill="var(--star)"><use href="#s"/><use href="#s" x="13"/><use href="#s" x="26"/></g><g fill="var(--star-off)"><use href="#s" x="39"/><use href="#s" x="52"/></g></svg></div><div class="links">+ Add to Wishlist &nbsp; + Add to Compare</div></div></div>
</section>
<div class="abs arrow" style="left:68px"><svg width="8" height="12" viewBox="0 0 8 12"><path d="M6 1L2 6l4 5" fill="none" stroke="#fff" stroke-width="2.2"/></svg></div>
<div class="abs arrow" style="left:637px"><svg width="8" height="12" viewBox="0 0 8 12"><path d="M2 1l4 5-4 5" fill="none" stroke="#fff" stroke-width="2.2"/></svg></div>

<section class="about">
  <h2>About Us</h2>
  <p>Sed ut perspiciatis unde omnis iste natus error sit voluptatem accusantium doloremque laudantium, totam rem aperiam, eaque ipsa quae ab illo inventore veritatis et quasi architecto beatae vitae dicta sunt explicabo. Nemo enim ipsam voluptatem quia voluptas sit aspernatur aut odit aut fugit, sed quia consequuntur magni dolores eos qui ratione voluptatem sequi nesciunt. Neque porro quisquam est, qui dolorem ipsum quia dolor sit amet, consectetur, adipisci velit, sed quia non numquam eius modi tempora incidunt ut labore et of us ever undertakes laborious physical exercise,dolore magnam aliquam quaerat</p>
</section>
<a class="abs readmore">Read more</a>

<section class="abs brands">
  <svg style="left:10px" width="10" height="14" viewBox="0 0 10 14"><path d="M8 1L2 7l6 6" fill="none" stroke="#aaa" stroke-width="2"/></svg>
  <span class="name" style="left:58px;color:#1b3f91;font-weight:700;letter-spacing:1px">NORVANE</span>
  <span class="name" style="left:160px;color:#0a3a8c;font-weight:700">Kestrel</span>
  <span class="name" style="left:270px;color:#444">Lumenar</span>
  <span class="name" style="left:378px;color:#444;font-size:12px;top:12px">Tidefin</span>
  <span class="name" style="left:452px;color:#d7202a;font-weight:700">ORVEXA</span>
  <svg style="left:560px" width="10" height="14" viewBox="0 0 10 14"><path d="M2 1l6 6-6 6" fill="none" stroke="#888" stroke-width="2"/></svg>
</section>

<footer class="abs footer">
  <h5 style="left:69px">Contact Us</h5>
  <span class="dot" style="left:67px;top:38px"><svg width="10" height="10" viewBox="0 0 10 10"><path d="M2 1l2 2-1 1.5c.8 1.2 1.5 2 2.5 2.5L7 6l2 2-1.5 1.5C5 9 1 5 .5 2z" fill="#fff"/></svg></span>
  <div class="line" style="left:95px;top:37px">+3(345) 44.67.210<br>+3(345) 44.67.210</div>
  <span class="dot" style="left:67px;top:74px"><svg width="10" height="8" viewBox="0 0 10 8"><rect x="0" y="0" width="10" height="8" fill="#fff"/><path d="M0 0l5 4 5-4" fill="none" stroke="var(--orange)"/></svg></span>
  <div class="line" style="left:95px;top:70px">store@qbmail.com<br>sales@qbmail.com</div>
  <span class="dot" style="left:67px;top:107px"><svg width="10" height="10" viewBox="0 0 10 10"><path d="M5 0L0 5h1.5v5h2.5V7h2v3h2.5V5H10z" fill="#fff"/></svg></span>
  <div class="line" style="left:95px;top:103px">West 14th Elm Street,<br>Denver, 802140, U.S.A.</div>
  <span class="social" style="left:69px;background:#55acee"></span>
  <span class="social" style="left:98px;background:#3b5998"></span>
  <span class="social" style="left:128px;background:#f26522"></span>

  <h5 style="left:213px">Site Links</h5>
  <ul style="left:216px"><li>Home</li><li>Create</li><li>About</li><li>Contact</li><li>Request a Quote</li></ul>

  <h5 style="left:338px">Shipping Info</h5>
  <ul style="left:339px"><li>Site Map</li><li>Search Terms</li><li>Advanced Search</li><li>Mobile</li><li>Contact Us</li><li>Advanced Search</li></ul>

  <h5 style="left:461px">Newsletter</h5>
  <div class="email">Enter your email address</div>
  <div class="submit">Submit</div>
  <svg style="position:absolute;left:461px;top:68px" width="140" height="30" viewBox="0 0 140 30"><rect x="0" y="4" width="42" height="22" fill="#eee"/><rect x="48" y="4" width="46" height="22" rx="2" fill="#3a3a3a"/><circle cx="124" cy="15" r="14" fill="#f4c21a"/></svg>
  <svg style="position:absolute;left:462px;top:112px" width="165" height="15" viewBox="0 0 165 15"><rect x="0" y="0" width="24" height="14" rx="2" fill="#2c4e8a"/><rect x="28" y="0" width="24" height="14" rx="2" fill="#1b8fd0"/><rect x="56" y="0" width="24" height="14" rx="2" fill="#ddd"/><rect x="84" y="0" width="24" height="14" rx="2" fill="#2a78c8"/><rect x="112" y="0" width="24" height="14" rx="2" fill="#e8e8e8"/><rect x="140" y="0" width="24" height="14" rx="2" fill="#1a3d8f"/></svg>
</footer>
<div class="copy">© 2013.qbbrightpathsolutions.com</div>

</body>
</html>
```